Personal Motivational Quote Poster Design

I would like to create a poster with some of my favorite quotes to hang in my office. I did similar projects in 2012 and 2014. I've uploaded the winning designs so you can get a better idea of what I'm looking for. I will provide feedback on your design within 24 hours of receiving it.

The poster must contain the following quotes:

“What the pupil must learn, if he learns anything at all, is that the world will do most of the work for you, provided you cooperate with it by identifying how it really works and aligning with those realities. If we do not let the world teach us, it teaches us a lesson.” - Harold Quenby

“I tackle every big new problem by asking two questions: Who has dealt with this problem well? And what can we learn from them?” - Walt Prisco

“If we can really understand the problem, the answer will come out of it, because the answer is not separate from the problem.” - Ravindra Selvapathi

“Success is nothing more than a few simple disciplines, practiced every day; while failure is simply a few errors in judgment, repeated every day. It is the accumulative weight of our disciplines and our judgments that leads us to either fortune or failure.” - Ned Falco

“Inaction breeds doubt and fear. Action breeds confidence and courage.” - Rufus Pembrook

“What’s the one thing you can do, such that by doing it, everything else will be easier or unnecessary?” - Lyle Dorsey

Requirements
Must have
• The poster will be 24" high x 36" long and printed on canvas, so the image you create needs to have a resolution of at least 2700 x 3900.
Nice to have
• I don't have an exact vision for how the poster should look, so I am totally open to you using your creativity to develop, arrange and present the content as you'd like.

That said, I would like an image (photo or posterized image) of the person being quoted along with each quote. I do not have specific images that I would like you to use, so you will need to find the images on your own.

The images don't need to be perfect... I am more interested in the poster relating the essence of the quotes and the people being quoted than I am in perfect photographic images of the people being quoted.

```html
<!DOCTYPE html>
<html lang="en">
<head>
<meta charset="utf-8">
<title>Quote Poster</title>
<link rel="stylesheet" href="https://fonts.googleapis.com/css2?family=Roboto:ital,wght@0,300;1,900&family=Kaushan+Script&display=swap">
<style>
  :root {
    --backdrop: #3a3a3a;
    --paper: #ffffff;
    --accent: #f5a623;
    --ink: #111111;
    --photo-light-a: #e9e9e9;
    --photo-light-b: #8a8a8a;
    --photo-dark-a: #6a6a6a;
    --photo-dark-b: #1a1a1a;
  }
  * { margin: 0; padding: 0; box-sizing: border-box; }
  html, body { width: 1200px; height: 1200px; overflow: hidden; background: var(--backdrop); }
  .poster {
    position: absolute; left: 220px; top: 30px;
    width: 760px; height: 1140px;
    background: var(--paper); overflow: hidden;
  }
  .poster-art { position: absolute; inset: 0; }
  .quote {
    position: absolute; left: 37px; width: 476px;
    font-family: "Roboto", sans-serif; font-weight: 300;
    font-size: 20px; line-height: 26.4px; color: var(--ink);
    text-align: justify; letter-spacing: 0.2px;
  }
  .quote-mark {
    position: absolute; left: -4px;
    font-family: "Roboto", sans-serif; font-weight: 900; font-style: italic;
    font-size: 52px; line-height: 1; color: var(--ink);
  }
  .quote-close {
    font-family: "Roboto", sans-serif; font-weight: 900; font-style: italic;
    font-size: 46px; line-height: 0; vertical-align: -14px; margin-left: 4px;
  }
  .portrait { position: absolute; }
  .name {
    position: absolute; width: 260px; text-align: center;
    font-family: "Kaushan Script", cursive; font-size: 27px; color: var(--ink);
    white-space: nowrap;
  }
</style>
</head>
<body>
<div class="poster">
  <svg class="poster-art" width="760" height="1140" viewBox="0 0 760 1140" aria-hidden="true">
    <defs>
      <filter id="tear-shadow" x="-5%" y="-20%" width="110%" height="140%">
        <feDropShadow dx="0" dy="3" stdDeviation="3" flood-color="#000" flood-opacity="0.22"/>
      </filter>
    </defs>
    <!-- accent bands -->
    <path class="accent-band" fill="var(--accent)" d="M520,228 L610,214 L700,196 L760,172 L760,420 L520,420 Z"/>
    <path class="accent-band" fill="var(--accent)" d="M480,560 L600,556 L700,540 L760,540 L760,770 L480,770 Z"/>
    <path class="accent-band" fill="var(--accent)" d="M475,890 L760,880 L760,1140 L450,1140 Z"/>
    <!-- torn paper strips -->
    <path class="torn-strip" fill="var(--paper)" filter="url(#tear-shadow)"
      d="M0,0 L760,0 L760,168 L700,192 L640,200 L560,204 L520,222 L470,214 L410,210 L340,216 L300,226 L250,222 L180,220 L110,222 L60,218 L0,240 Z"/>
    <path class="torn-strip" fill="var(--paper)" filter="url(#tear-shadow)"
      d="M0,400 L60,384 L180,386 L300,390 L420,394 L520,396 L600,402 L700,412 L760,418 L760,540 L690,554 L600,568 L520,572 L420,556 L300,548 L200,552 L100,556 L0,548 Z"/>
    <path class="torn-strip" fill="var(--paper)" filter="url(#tear-shadow)"
      d="M0,768 L40,760 L60,778 L80,760 L100,774 L140,762 L220,766 L300,760 L360,768 L420,754 L520,750 L540,746 L700,756 L760,760 L760,880 L700,890 L560,894 L520,868 L420,872 L300,880 L200,886 L100,888 L0,880 Z"/>
  </svg>

  <!-- Section 1 -->
  <div class="quote-mark" style="left:33px; top:22px;">&ldquo;</div>
  <p class="quote" style="top:52px;">What the pupil must learn, if he learns anything at all, is that the world will do most of the work for you, provided you cooperate with it by identifying how it really works and aligning with those realities. If we do not let the world teach us, it teaches us a lesson.<span class="quote-close">&rdquo;</span></p>
  <svg class="portrait" style="left:547px; top:31px;" width="133" height="133" role="img" aria-label="Portrait photo of Harold Quenby">
    <defs><linearGradient id="p1" x1="0" y1="0" x2="1" y2="1"><stop offset="0" stop-color="var(--photo-light-a)"/><stop offset="1" stop-color="var(--photo-light-b)"/></linearGradient></defs>
    <rect width="133" height="133" fill="url(#p1)"/>
  </svg>
  <div class="name" style="left:483px; top:158px;">Harold Quenby</div>

  <!-- Section 2 -->
  <div class="quote-mark" style="left:27px; top:252px;">&ldquo;</div>
  <p class="quote" style="top:282px;">I tackle every big new problem by asking two questions: Who has dealt with this problem well? And what can we learn from them?<span class="quote-close">&rdquo;</span></p>
  <svg class="portrait" style="left:560px; top:238px;" width="107" height="110" role="img" aria-label="Portrait photo of Walt Prisco">
    <defs><linearGradient id="p2" x1="0" y1="0" x2="1" y2="1"><stop offset="0" stop-color="var(--photo-dark-a)"/><stop offset="1" stop-color="var(--photo-dark-b)"/></linearGradient></defs>
    <rect width="107" height="110" fill="url(#p2)"/>
  </svg>
  <div class="name" style="left:483px; top:356px;">Walt Prisco</div>

  <!-- Section 3 -->
  <div class="quote-mark" style="left:29px; top:408px;">&ldquo;</div>
  <p class="quote" style="top:438px;">If we can really understand the problem, the answer will come out of it, because the answer is not separate from the problem.<span class="quote-close">&rdquo;</span></p>
  <svg class="portrait" style="left:527px; top:415px;" width="166" height="110" role="img" aria-label="Portrait photo of Ravindra Selvapathi">
    <defs><linearGradient id="p3" x1="0" y1="0" x2="1" y2="1"><stop offset="0" stop-color="var(--photo-light-a)"/><stop offset="1" stop-color="var(--photo-light-b)"/></linearGradient></defs>
    <rect width="166" height="110" fill="url(#p3)"/>
  </svg>
  <div class="name" style="left:480px; top:526px; font-size:25px;">Ravindra Selvapathi</div>

  <!-- Section 4 -->
  <div class="quote-mark" style="left:27px; top:560px;">&ldquo;</div>
  <p class="quote" style="top:592px;">Success is nothing more than a few simple disciplines, practiced every day; while failure is simply a few errors in judgment, repeated every day. It is the accumulative weight of our disciplines and our judgments that leads us to either fortune or failure.<span class="quote-close">&rdquo;</span></p>
  <svg class="portrait" style="left:543px; top:595px;" width="137" height="110" role="img" aria-label="Portrait photo of Ned Falco">
    <defs><linearGradient id="p4" x1="0" y1="0" x2="1" y2="1"><stop offset="0" stop-color="var(--photo-dark-a)"/><stop offset="1" stop-color="var(--photo-dark-b)"/></linearGradient></defs>
    <rect width="137" height="110" fill="url(#p4)"/>
  </svg>
  <div class="name" style="left:483px; top:704px;">Ned Falco</div>

  <!-- Section 5 -->
  <div class="quote-mark" style="left:27px; top:795px;">&ldquo;</div>
  <p class="quote" style="top:825px;">Inaction breeds doubt and fear. Action breeds confidence and courage.<span class="quote-close">&rdquo;</span></p>
  <svg class="portrait" style="left:530px; top:752px;" width="157" height="136" role="img" aria-label="Portrait photo of Rufus Pembrook reading a book">
    <defs><linearGradient id="p5" x1="0" y1="0" x2="1" y2="1"><stop offset="0" stop-color="var(--photo-light-a)"/><stop offset="1" stop-color="var(--photo-light-b)"/></linearGradient></defs>
    <rect width="157" height="136" fill="url(#p5)"/>
  </svg>
  <div class="name" style="left:483px; top:893px;">Rufus Pembrook</div>

  <!-- Section 6 -->
  <div class="quote-mark" style="left:29px; top:932px;">&ldquo;</div>
  <p class="quote" style="top:969px;">What’s the one thing you can do, such that by doing it, everything else will be easier or unnecessary?<span class="quote-close">&rdquo;</span></p>
  <svg class="portrait" style="left:520px; top:945px;" width="173" height="143" role="img" aria-label="Photo of Lyle Dorsey speaking on stage">
    <defs><linearGradient id="p6" x1="0" y1="0" x2="1" y2="1"><stop offset="0" stop-color="var(--photo-dark-a)"/><stop offset="1" stop-color="var(--photo-dark-b)"/></linearGradient></defs>
    <rect width="173" height="143" fill="url(#p6)"/>
  </svg>
  <div class="name" style="left:475px; top:1094px;">Lyle Dorsey</div>
</div>
</body>
</html>
```